Digital Marketing Website Redesign, modern, fresh, dynamic

Hi there, we would like to freshen up our website and create a new dynamic look. We are a digital marketing agency who specialise in digital transformation in the form of creating websites for appointment bookings. Our clients are service businesses such as hairdressers, dentists and doctors who's patients need to book appointments with them.

Our company name is Tallomex with the point being we can help increase your revenue curve by increasing your appointment bookings.

Our services include building the website, creating campaigns to drive traffic, increasing conversions and monitoring and reporting.

We are playing with a tagline of 'Step into your Digital Transformation' as we have a 5 step journey that customers can take with us getting them from zero to full appointment bookings.

Our current website is www.tallomex-sample.com

You can see a draft design that I mocked up on Canva here https://www.draftboard-sample.com/design/QXB82LmpR7T/KpoW39dnFsYbZet_wqe_OPa/edit?utm_content=QXB82LmpR7T&utm_campaign=designshare&utm_medium=link2&utm_source=sharebutton

Also attached some other homepage ideas. In regard to photos we are open to ideas.

Please let if you need any more information to provide us with an initial design. Thanks million and I look forward to receiving fantastic designs :)

Marian Dobbs
Tallomex

Target Market(s)

Appointment based businesses such as hairdressers, dentists, doctors

Industry/Entity Type

Marketing and Digital

Coding

Coded - Design and coding required

Number of Pages Required

1 page

Colors
0094D4
00A9DD
6FCCEA
C7EBF8
E9F6FB

Requirements
Must have
• Appointment booking CTA
Nice to have
• A website we like https://www.fergalwhitty-sample.ie

```html
<!DOCTYPE html>
<html lang="en">
<head>
<meta charset="utf-8">
<title>Tallomex – Step into your Digital Transformation</title>
<link href="https://fonts.googleapis.com/css2?family=Poppins:wght@400;500;600;700;800&display=swap" rel="stylesheet">
<style>
:root{
  --blue:#0094D4;
  --cyan:#00A9DD;
  --sky:#6FCCEA;
  --pale:#C7EBF8;
  --mist:#E9F6FB;
  --yellow:#D6DB22;
  --ink:#1d2430;
  --text:#3b4250;
  --navy:#24457a;
  --black:#0d0d0f;
}
*{box-sizing:border-box;margin:0;padding:0}
html,body{width:1200px;height:4418px;overflow:hidden}
body{font-family:"Poppins",sans-serif;color:var(--text);background:#fff;position:relative}
.abs{position:absolute}
.btn{position:absolute;background:var(--yellow);color:var(--navy);font-weight:700;font-size:16px;display:flex;align-items:center;justify-content:center;gap:12px}
.btn .arrow{width:18px;height:18px;border-radius:50%;background:var(--navy);color:var(--yellow);font-size:12px;display:flex;align-items:center;justify-content:center}

/* header */
.site-header{position:absolute;top:0;left:0;width:1200px;height:101px;background:#fff}
.brand{position:absolute;left:75px;top:26px;display:flex;align-items:center;gap:10px}
.brand-mark{width:22px;height:22px;border-radius:50%;background:var(--yellow)}
.brand-name{font-weight:700;font-size:32px;color:var(--navy);line-height:1}
.brand-sub{position:absolute;left:135px;top:80px;font-size:10px;color:var(--navy);font-weight:500}
.nav{position:absolute;left:457px;top:44px;display:flex;gap:34px;font-size:13px;color:var(--ink)}
.header-cta{left:910px;top:28px;width:216px;height:46px;font-size:14px}

/* hero */
.hero{position:absolute;top:101px;left:0;width:1200px;height:610px;overflow:hidden;background:linear-gradient(100deg,var(--blue) 0%,#1a9fd3 45%,var(--sky) 100%)}
.hero-frame{position:absolute;left:600px;top:-110px;width:560px;height:560px;transform:rotate(45deg);border-radius:60px;background:#1f6ea6;opacity:.55}
.hero-photo{position:absolute;left:640px;top:-80px;width:520px;height:520px;transform:rotate(45deg);border-radius:56px;background:radial-gradient(circle at 50% 50%,#bff3ff 0%,#3fb3e6 22%,#0d3c6e 60%,#06193a 100%)}
.hero h1{position:absolute;left:75px;top:110px;width:620px;font-size:53px;line-height:52px;font-weight:800;color:#fff}
.hero p{position:absolute;left:75px;top:236px;width:520px;font-size:16.5px;line-height:28px;color:#fff}
.hero .btn{left:75px;top:376px;width:166px;height:48px}
.hero-wave{position:absolute;left:0;bottom:0;width:1200px;height:90px}

/* stats */
.stats{position:absolute;top:771px;left:75px;width:1051px;display:flex;justify-content:space-between}
.stat{width:241px;height:241px;border-radius:50%;background:var(--cyan);color:#fff;display:flex;flex-direction:column;align-items:center;justify-content:center;text-align:center}
.stat:nth-child(2),.stat:nth-child(4){background:var(--blue)}
.stat svg{width:44px;height:44px;margin-bottom:8px}
.stat-num{font-size:48px;font-weight:800;line-height:1.1}
.stat-label{font-size:14px;font-weight:600;line-height:21px;margin-top:6px}

/* testimonials */
.band{position:absolute;left:0;width:1200px;background:var(--mist)}
.band svg.wave{position:absolute;left:0;width:1200px}
.section-title{position:absolute;left:0;width:1200px;text-align:center;font-size:32px;font-weight:700;color:var(--ink)}
.reviews{position:absolute;top:1277px;left:75px;width:1051px;display:flex;justify-content:space-between}
.review{width:329px;height:363px;background:#fff;text-align:center;padding-top:40px}
.stars{color:#f4b400;font-size:19px;letter-spacing:4px}
.review h3{color:var(--cyan);font-size:17px;font-weight:700;margin-top:8px}
.review p{font-size:13.5px;line-height:21px;width:275px;margin:12px auto 0}
.avatar{width:84px;height:84px;border-radius:50%;margin:18px auto 0;background:linear-gradient(160deg,#d9dde3,#6b6f78)}
.review h4{color:var(--blue);font-size:16px;font-weight:700;margin-top:14px}
.review .role{font-size:13.5px;margin-top:2px}

/* steps */
.steps{position:absolute;top:1899px;left:75px;width:1051px;display:flex;justify-content:space-between}
.step{width:329px;height:213px;position:relative;display:flex;flex-direction:column;align-items:center;justify-content:center;color:#fff;text-align:center}
.step:nth-child(1){background:linear-gradient(135deg,#6d6a63,#a69e8e 60%,#5a6678)}
.step:nth-child(2){background:linear-gradient(135deg,#3b414d,#707684 60%,#4d5563)}
.step:nth-child(3){background:linear-gradient(135deg,#8b8c8f,#b4b5b8 60%,#6a6c72)}
.step-tag{background:rgba(20,20,20,.6);border:1px solid #fff;border-radius:12px;font-size:11px;padding:2px 12px;margin-bottom:6px}
.step-title{font-size:28px;font-weight:700;line-height:28px}
.signup{left:518px;top:2168px;width:164px;height:48px}

/* team */
.team-intro{position:absolute;top:2440px;left:100px;width:1000px;text-align:center;font-size:14.5px;line-height:26px}
.team{position:absolute;top:2520px;left:75px;width:1051px;display:grid;grid-template-columns:repeat(3,1fr)}
.member{height:274px;text-align:center;padding-top:0}
.member:nth-child(-n+3){border-bottom:1px solid var(--pale)}
.member:nth-child(3n+1),.member:nth-child(3n+2){border-right:1px solid var(--pale)}
.member:nth-child(n+4){padding-top:24px}
.member .avatar{width:171px;height:171px;margin:0 auto}
.member h3{color:var(--cyan);font-size:23px;font-weight:700;margin-top:22px;line-height:1.1}
.member .role{font-size:14.5px;margin-top:4px}

/* pricing */
.pricing-sub{position:absolute;top:3296px;left:0;width:1200px;text-align:center;font-size:14.5px}
.plans{position:absolute;top:3351px;left:75px;width:1051px;display:flex;justify-content:space-between}
.plan{width:329px;height:355px;background:var(--cyan);border-radius:24px;color:#fff;padding:36px 20px 0}
.plan h3{text-align:center;font-size:22px;font-weight:700}
.price{text-align:center;font-size:62px;font-weight:800;line-height:1;margin-top:6px}
.per{text-align:center;font-size:21px;font-weight:700;margin-top:-2px}
.plan ul{list-style:none;font-size:14px;line-height:25px;margin-top:20px;min-height:100px}
.plan li{margin-bottom:8px}
.plan li b{font-weight:700}
.plan .indent{padding-left:58px;margin-top:-8px}
.plan-btn{width:260px;height:46px;margin:0 auto;border:2px solid #fff;display:flex;align-items:center;justify-content:center;gap:14px;font-weight:700;font-size:16px}
.plan-btn .arrow{width:18px;height:18px;border-radius:50%;background:#fff;color:var(--cyan);font-size:12px;display:flex;align-items:center;justify-content:center}
.more-info{left:435px;top:3771px;width:330px;height:44px;font-size:15px}

/* footer */
.footer{position:absolute;top:3900px;left:0;width:1200px;height:518px;background:var(--black)}
.footer svg.wave{position:absolute;top:-2px;left:0;width:1200px;height:80px}
.fcol{position:absolute;top:136px;color:#fff;font-size:14px;line-height:22px}
.fcol h4{color:var(--cyan);font-size:20px;font-weight:700;line-height:26px;margin-bottom:12px}
.fcol p{margin-bottom:16px}
.socials{display:flex;gap:14px;margin-bottom:40px}
.socials span{width:18px;height:18px;border-radius:50%;background:#fff}
.hours{display:grid;grid-template-columns:172px auto;row-gap:12px}
.legal{position:absolute;top:436px;left:0;width:1200px;border-top:1px solid #2a2a2e;padding-top:34px;text-align:center;font-size:13px;color:#8b8f98}
</style>
</head>
<body>

<header class="site-header">
  <div class="brand"><span class="brand-mark"></span><span class="brand-name">Tallomex</span></div>
  <div class="brand-sub">Digital Transformation Consultancy</div>
  <nav class="nav"><span>5 steps</span><span>Our Pricing</span><span>Ahead of the Curve</span><span>Our Team</span></nav>
  <div class="btn header-cta">Book An Appointment</div>
</header>

<section class="hero">
  <div class="hero-frame"></div>
  <div class="hero-photo" role="img" aria-label="Person walking into a glowing digital tunnel"></div>
  <h1>Step into your Digital Transformation</h1>
  <p>Digital transformation is a journey. At Tallomex we divide the journey into five key steps that take your business from comprehensive market research to full appointment bookings. Ready to go on that journey?</p>
  <div class="btn">Start Here</div>
  <svg class="hero-wave" viewBox="0 0 1200 90" preserveAspectRatio="none"><path d="M0 90 L0 62 C220 20 420 10 640 40 C860 72 1020 70 1200 30 L1200 90 Z" fill="#fff"/></svg>
</section>

<section class="stats">
  <div class="stat">
    <svg viewBox="0 0 24 24" fill="none" stroke="#fff" stroke-width="2"><rect x="3" y="5" width="18" height="16" rx="2"/><path d="M3 10h18M8 3v4M16 3v4"/><path d="M7 14h2M11 14h2M15 14h2M7 17h2M11 17h2M15 17h2" stroke-width="1.8"/></svg>
    <div class="stat-num">762</div><div class="stat-label">Appointments<br>Booked</div>
  </div>
  <div class="stat">
    <svg viewBox="0 0 24 24" fill="none" stroke="#fff" stroke-width="2"><rect x="4" y="4" width="16" height="12" rx="1"/><path d="M2 19h20"/></svg>
    <div class="stat-num">31</div><div class="stat-label">Marketing<br>Campaigns</div>
  </div>
  <div class="stat">
    <svg viewBox="0 0 24 24" fill="none" stroke="#fff" stroke-width="2"><path d="M3 3v18h18M8 17v-5M12 17V8M16 17v-7M20 17V6"/></svg>
    <div class="stat-num">25%</div><div class="stat-label">Website Traffic<br>Increase</div>
  </div>
  <div class="stat">
    <svg viewBox="0 0 24 24" fill="none" stroke="#fff" stroke-width="2"><path d="M9 18h6M10 21h4M12 3a6 6 0 0 0-4 10.5c.8.8 1 1.6 1 2.5h6c0-.9.2-1.7 1-2.5A6 6 0 0 0 12 3z"/></svg>
    <div class="stat-num">25%</div><div class="stat-label">Creative<br>Ideas</div>
  </div>
</section>

<section class="band" style="top:1080px;height:680px">
  <svg class="wave" style="top:0;height:70px" viewBox="0 0 1200 70" preserveAspectRatio="none"><path d="M0 0 H1200 V20 C1000 50 800 60 600 40 C380 20 180 10 0 35 Z" fill="#fff"/></svg>
  <svg class="wave" style="bottom:0;height:80px" viewBox="0 0 1200 80" preserveAspectRatio="none"><path d="M0 80 V30 C200 60 420 70 640 50 C860 30 1020 10 1200 40 V80 Z" fill="#fff"/></svg>
</section>
<h2 class="section-title" style="top:1204px">Why others choose us?</h2>
<section class="reviews">
  <article class="review">
    <div class="stars">★★★★★</div>
    <h3>100 bookings in first month!</h3>
    <p>Tallomex's booking system helped us get over 100 appointment bookings in May 2020.</p>
    <div class="avatar" role="img" aria-label="Portrait of Lorna Quill"></div>
    <h4>Lorna Quill</h4><div class="role">Owner, Shear Bloom</div>
  </article>
  <article class="review">
    <div class="stars">★★★★★</div>
    <h3>100 bookings in first month!</h3>
    <p>Tallomex's booking system helped us get over 100 appointment bookings in May 2020.</p>
    <div class="avatar" role="img" aria-label="Portrait of Dr. Haro-Linde"></div>
    <h4>Dr. Haro-Linde</h4><div class="role">Owner, Brightbite</div>
  </article>
  <article class="review">
    <div class="stars">★★★★★</div>
    <h3>100 bookings in first month!</h3>
    <p>Tallomex's booking system helped us get over 100 appointment bookings in May 2020.</p>
    <div class="avatar" role="img" aria-label="Portrait of Lorna Quill"></div>
    <h4>Lorna Quill</h4><div class="role">Owner, Shear Bloom</div>
  </article>
</section>

<h2 class="section-title" style="top:1828px">5 Steps</h2>
<section class="steps">
  <div class="step" role="img" aria-label="Team planning creative campaigns at a desk"><span class="step-tag">#ONE</span><span class="step-title">Creative<br>Campaigns</span></div>
  <div class="step" role="img" aria-label="People reviewing market research charts"><span class="step-tag">#TWO</span><span class="step-title">Market<br>Research</span></div>
  <div class="step" role="img" aria-label="Hand holding a phone showing an online booking screen"><span class="step-tag">#THREE</span><span class="step-title">Online<br>Bookings</span></div>
</section>
<div class="btn signup">Sign Up</div>

<section class="band" style="top:2280px;height:870px">
  <svg class="wave" style="top:0;height:60px" viewBox="0 0 1200 60" preserveAspectRatio="none"><path d="M0 0 H1200 V10 C1000 30 820 40 600 25 C380 10 200 20 0 50 Z" fill="#fff"/></svg>
  <svg class="wave" style="bottom:0;height:70px" viewBox="0 0 1200 70" preserveAspectRatio="none"><path d="M0 70 V20 C220 50 420 60 640 40 C860 20 1020 10 1200 35 V70 Z" fill="#fff"/></svg>
</section>
<h2 class="section-title" style="top:2380px">Our Team</h2>
<p class="team-intro">From business management and web development to creative campaign delivery and social media expertise, our team has all the experience your business needs to it to the top of its digital game.</p>
<section class="team">
  <div class="member"><div class="avatar" role="img" aria-label="Portrait of Declan"></div><h3>Declan</h3><div class="role">Account Manager</div></div>
  <div class="member"><div class="avatar" role="img" aria-label="Portrait of Rowan"></div><h3>Rowan</h3><div class="role">Account Manager</div></div>
  <div class="member"><div class="avatar" role="img" aria-label="Portrait of Nessa"></div><h3>Nessa</h3><div class="role">Account Manager</div></div>
  <div class="member"><div class="avatar" role="img" aria-label="Portrait of Kiran"></div><h3>Kiran</h3><div class="role">Web developer</div></div>
  <div class="member"><div class="avatar" role="img" aria-label="Portrait of Marian"></div><h3>Marian</h3><div class="role">Content Creator</div></div>
  <div class="member"><div class="avatar" role="img" aria-label="Portrait of Selene"></div><h3>Selene</h3><div class="role">Social Media Specialist</div></div>
</section>

<h2 class="section-title" style="top:3235px">Our Pricing</h2>
<p class="pricing-sub">Which plan you take will depend on how many steps you want to take on your digital transformation journey.</p>
<section class="plans">
  <div class="plan">
    <h3>Starter Plan</h3><div class="price">€399</div><div class="per">Month</div>
    <ul><li><b>Step 1:</b>&nbsp; Online readiness review based</li><li class="indent">on our 12 point checklist</li><li><b>Step 2:</b> Implementation</li></ul>
    <div class="plan-btn">Take 2 Steps <span class="arrow">➜</span></div>
  </div>
  <div class="plan">
    <h3>Premium Plan</h3><div class="price">€599</div><div class="per">Month</div>
    <ul><li>Steps 1 &amp; 2</li><li><b>Step 3:</b> Content is King</li></ul>
    <div class="plan-btn">Take 3 Steps <span class="arrow">➜</span></div>
  </div>
  <div class="plan">
    <h3>Ultimate Plan</h3><div class="price">€899</div><div class="per">Month</div>
    <ul><li>Steps 1 &amp; 2</li><li><b>Step 4:</b> Marketing Campaign</li><li><b>Step 5:</b> Monitor and Maintain</li></ul>
    <div class="plan-btn">Take the Full Journey <span class="arrow">➜</span></div>
  </div>
</section>
<div class="btn more-info">More info about the five steps <span class="arrow">➜</span></div>

<footer class="footer">
  <svg class="wave" viewBox="0 0 1200 80" preserveAspectRatio="none"><path d="M0 0 H1200 V10 C980 50 760 20 560 12 C340 4 160 20 0 40 Z" fill="#fff"/></svg>
  <div class="fcol" style="left:75px;width:300px">
    <h4>Harbourgate Enterprise<br>Hub</h4>
    <p>Northshore Institute of Technology,<br>Ballykeel, Co. Westmere<br>Ireland W00 X1YZ</p>
    <h4 style="margin-top:28px">Contact Us</h4>
    <p>Tel: +353 1 555 0140</p>
    <p>Email. info@tallomex-sample.com</p>
  </div>
  <div class="fcol" style="left:434px;width:330px">
    <h4>Quick Contact</h4>
    <p>General Enquiries:&nbsp; +353 1 555 0140</p>
    <p>Customer Service:&nbsp; +353 1 555 0170</p>
    <p>Investor Enquiries:&nbsp; +353 1 555 0190</p>
  </div>
  <div class="fcol" style="left:819px;width:320px">
    <h4>Follow Us</h4>
    <div class="socials"><span></span><span></span><span></span><span></span><span></span></div>
    <h4>Opening Hours (CET)</h4>
    <div class="hours"><span>Monday – Friday</span><span>8.30am – 6.30pm</span><span>Saturday</span><span>Closed</span><span>Sunday</span><span>Closed</span></div>
  </div>
  <div class="legal">© 2024 Sitemap Terms &amp; Conditions Privacy Policy Cookies Policy Acceptable Use Policy</div>
</footer>

</body>
</html>
```